Construction material supplies company business card ****

1. Full company name “K T Masonry Works Ltd”
I am after a Business card design for the company as a whole. We are better known in Solomon Islands as “K T Masonry” for short.

We are a building materials supplier of
Ready Mixed Concrete, Bricks and Blocks,
Quarry products- gravel, aggregates, sand etc.
Cement distributor/retailer of reputable brands.
Other prefab concrete products. Culverts, wave breakers, concrete retaining blocks etc.

2. Competitive Advantage over Competition: Quality, efficient, professional, dependable, reliable

3. We want people to feel trust worthy, high quality, strong when they see our brand

5. No preference to color. Maybe more sturdy and corporate. Not fancy.

Industry/Entity Type

CONSTRUCTION SUPPLY

Contact Information for Business Card

Name, Position, office phone mob phone, email

Requirements
Must have
• the company logo
Nice to have
• would like to see a mixture of designs, of with logo only and also with simple graphic designs to bring out the company whilst still have the strong sturdy professional feeling

```html
<!DOCTYPE html>
<html lang="en">
<head>
<meta charset="utf-8">
<title>K T Masonry – Business Card</title>
<link href="https://fonts.googleapis.com/css2?family=Roboto:wght@400;700&display=swap" rel="stylesheet">
<style>
  :root{
    --backdrop:#2b2b2b;
    --card-light:#e8e8e8;
    --card-mid:#d9d9d9;
    --brand-blue:#1c4872;
    --brand-blue-deep:#163c61;
    --text-light:#eef2f6;
  }
  *{margin:0;padding:0;box-sizing:border-box}
  html,body{width:1200px;height:1138px;overflow:hidden;background:var(--backdrop);font-family:'Roboto',sans-serif}
  .card{position:absolute;border-radius:14px;overflow:hidden;
    background:radial-gradient(ellipse at 50% 40%,var(--card-light),var(--card-mid));
    box-shadow:0 4px 10px rgba(0,0,0,.45)}
  .card--front{left:274px;top:186px;width:622px;height:376px}
  .card--back{left:276px;top:608px;width:618px;height:374px}

  .wordmark{position:absolute;display:flex;align-items:center;gap:18px;color:var(--brand-blue);
    font-weight:700;letter-spacing:2px;white-space:nowrap}
  .wordmark__square{display:block;background:var(--brand-blue)}
  .card--front .wordmark{left:0;right:0;justify-content:center;top:68px;font-size:50px}
  .card--front .wordmark__square{width:62px;height:62px}

  .band{position:absolute;left:0;right:0;top:213px;height:80px;background:var(--brand-blue)}
  .pill{position:absolute;left:136px;top:186px;width:348px;height:40px;border-radius:20px;
    background:var(--brand-blue);border:2px solid #e7ecf1;color:var(--text-light);
    font-size:16px;display:flex;align-items:center;justify-content:center}
  .offer{position:absolute;left:0;right:0;text-align:center;font-size:16px;line-height:22px}
  .offer--band{top:241px;color:var(--text-light)}
  .offer--lower{top:307px;color:var(--brand-blue);line-height:24px}

  .card--back .wordmark{left:44px;top:188px;font-size:38px}
  .logo-square{position:absolute;left:132px;top:70px;width:96px;height:96px;background:var(--brand-blue)}
  .person{position:absolute;right:34px;top:50px;text-align:right;color:var(--brand-blue)}
  .person__name{font-size:23px;font-weight:700;line-height:28px}
  .person__role{font-size:16px;line-height:22px}
  .person__address{font-size:16px;line-height:26px;margin-top:20px}
  .wave{position:absolute;left:0;top:0;width:618px;height:374px}
  .contacts{position:absolute;right:16px;top:268px;list-style:none;color:var(--text-light);font-size:16px}
  .contacts li{display:flex;justify-content:flex-end;align-items:center;gap:12px;height:26px}
  .contacts svg{width:15px;height:15px}
</style>
</head>
<body>

<section class="card card--front">
  <div class="wordmark"><span class="wordmark__square"></span>K T MASONRY</div>
  <div class="band"></div>
  <div class="pill">We are a building materials supplier of</div>
  <p class="offer offer--band">Ready Mixed Concrete, Bricks and Blocks, Quarry Products<br>Quarry Products:- Gravel, Aggregates, Sand Etc.</p>
  <p class="offer offer--lower">Cement Distributor/Retailer of Reputable Brands.<br>Other Concrete Products Culverts, Wave Breakers, Concrete Retaining Blocks</p>
</section>

<section class="card card--back">
  <svg class="wave" viewBox="0 0 618 374" aria-hidden="true">
    <path d="M0 300 C120 340 260 320 380 260 C470 215 540 200 618 204 L618 374 L0 374 Z" fill="var(--brand-blue-deep)"/>
    <path d="M0 322 C130 350 290 330 400 272 C480 232 550 212 618 212" fill="none" stroke="#e3e3e3" stroke-width="5"/>
    <path d="M50 310 C150 330 260 320 320 302" fill="none" stroke="#e3e3e3" stroke-width="3"/>
  </svg>
  <span class="logo-square"></span>
  <div class="wordmark">K T MASONRY</div>
  <div class="person">
    <p class="person__name">Daniel Harper</p>
    <p class="person__role">Managing Director</p>
    <p class="person__address">18 Harbour Rd., Any City,<br>Any Town 4021</p>
  </div>
  <ul class="contacts">
    <li>000 0000 0000
      <svg viewBox="0 0 16 16"><path d="M2 6c0-2 3-3 6-3s6 1 6 3v1h-3V6H5v1H2zM4 8h8l1 5H3z" fill="var(--text-light)"/></svg></li>
    <li>daniel@ktmasonry.com
      <svg viewBox="0 0 16 16"><rect x="1" y="3" width="14" height="10" fill="var(--text-light)"/><path d="M1 3l7 6 7-6" fill="none" stroke="var(--brand-blue-deep)" stroke-width="1.3"/></svg></li>
    <li>www.ktmasonry.com
      <svg viewBox="0 0 16 16"><circle cx="8" cy="8" r="6.5" fill="var(--text-light)"/><path d="M1.5 8h13M8 1.5v13M8 1.5c-3 3-3 10 0 13M8 1.5c3 3 3 10 0 13" fill="none" stroke="var(--brand-blue-deep)" stroke-width="1"/></svg></li>
  </ul>
</section>

</body>
</html>
```